Brell Stone Company Business Cards

Front and Back Business Card - logo and text setup - cool design. I need workable photoshop or illustrator files so I can setup each employee card with design that is created
Updates

Hi everyone, thank you for the great entries. Please no more white and blue cards - there are so many already - black and silver only now please. thanks!

Target Market(s)

Construction Industry - Facility Managers

Industry/Entity Type

Construction

Contact Information for Business Card

I really like contemporary simplistic looks - clean neat....not opposed to seeing some black backrounds

Requirements
Must have
• Logo/website address with design on front only - www.brellstone-example.com (logo attached)
• Back:
• Name/Title/Company Address/Phone/email address
Nice to have
• Cool design
Should not have
• Nothing gimmicky like Fire or Water - since we are a Fire Protection company - it has all been done

```html
<!DOCTYPE html>
<html lang="en">
<head>
<meta charset="utf-8">
<title>Brell Stone Company Business Cards</title>
<link rel="stylesheet" href="https://fonts.googleapis.com/css2?family=Roboto:wght@400;500;700&display=swap">
<style>
  :root {
    --page-bg: #d9d9d9;
    --silver-light: #e6e8ea;
    --silver-mid: #c3c7cc;
    --silver-dark: #9ea3a9;
    --card-black: #1b1c1e;
    --band-black: #141517;
    --text-light: #f2f3f4;
    --mark-dark: #0c0c0d;
  }
  * { margin: 0; padding: 0; box-sizing: border-box; }
  html, body {
    width: 1125px;
    height: 1200px;
    overflow: hidden;
    background: var(--page-bg);
    font-family: "Roboto", Arial, sans-serif;
  }
  .canvas { position: relative; width: 1125px; height: 1200px; }

  .card {
    position: absolute;
    left: 156px;
    width: 826px;
    height: 471px;
    overflow: hidden;
  }
  .card-front {
    top: 106px;
    background: linear-gradient(180deg, #f1f2f3 0%, var(--silver-light) 100%);
  }
  .card-back { top: 639px; background: var(--card-black); }

  .brand-name {
    position: absolute;
    left: 0;
    right: 0;
    text-align: center;
    font-weight: 700;
    font-size: 72px;
    line-height: 80px;
    letter-spacing: -1px;
  }
  .card-front .brand-name { top: 84px; color: var(--card-black); }
  .card-back .brand-name { top: 178px; color: var(--mark-dark); }

  .contact-band {
    position: absolute;
    left: 0;
    top: 277px;
    width: 100%;
    height: 194px;
    background: var(--band-black);
    border-top: 4px dotted var(--silver-mid);
  }

  .person {
    position: absolute;
    left: 49px;
    top: 42px;
    color: var(--text-light);
  }
  .person-name {
    font-weight: 500;
    font-size: 29px;
    color: var(--silver-mid);
    line-height: 34px;
  }
  .person-title { font-size: 20px; line-height: 26px; }
  .person-address { margin-top: 10px; font-size: 19px; line-height: 25px; }

  .contact-list {
    position: absolute;
    right: 48px;
    top: 57px;
    list-style: none;
    color: var(--text-light);
    font-size: 19px;
    line-height: 26px;
    text-align: right;
  }
  .contact-list li { display: flex; justify-content: flex-end; align-items: center; gap: 10px; }
  .contact-icon { width: 18px; height: 18px; fill: var(--silver-mid); flex: none; }
</style>
</head>
<body>
<div class="canvas">

  <section class="card card-front" aria-label="Business card front">
    <div class="brand-name">Brell Stone</div>

    <div class="contact-band">
      <div class="person">
        <div class="person-name">Daniel Reyes</div>
        <div class="person-title">CEO/Founder</div>
        <div class="person-address">48 Harbor Point Road<br>Millbrook, NY 10999</div>
      </div>

      <ul class="contact-list">
        <li>(555) 014-2210
          <svg class="contact-icon" viewBox="0 0 24 24" aria-hidden="true"><path d="M6.6 10.8a15.1 15.1 0 0 0 6.6 6.6l2.2-2.2a1 1 0 0 1 1-.25 11.4 11.4 0 0 0 3.6.57 1 1 0 0 1 1 1V20a1 1 0 0 1-1 1A17 17 0 0 1 3 4a1 1 0 0 1 1-1h3.5a1 1 0 0 1 1 1c0 1.25.2 2.45.57 3.57a1 1 0 0 1-.25 1z"/></svg>
        </li>
        <li>(555) 014-2216
          <svg class="contact-icon" viewBox="0 0 24 24" aria-hidden="true"><path d="M7 3h10v5H7z"/><path d="M4 9h16a2 2 0 0 1 2 2v6h-4v4H6v-4H2v-6a2 2 0 0 1 2-2zm4 7v3h8v-3z"/></svg>
        </li>
        <li>info@brellstone-example.com
          <svg class="contact-icon" viewBox="0 0 24 24" aria-hidden="true"><path d="M3 5h18a1 1 0 0 1 1 1v1l-10 6L2 7V6a1 1 0 0 1 1-1z"/><path d="M2 9.3l10 6 10-6V18a1 1 0 0 1-1 1H3a1 1 0 0 1-1-1z"/></svg>
        </li>
        <li>www.brellstone-example.com
          <svg class="contact-icon" viewBox="0 0 24 24" aria-hidden="true"><circle cx="12" cy="12" r="10"/></svg>
        </li>
      </ul>
    </div>
  </section>

  <section class="card card-back" aria-label="Business card back">
    <div class="brand-name">Brell Stone</div>
  </section>

</div>
</body>
</html>
```